BrindleStaffing Business Card Design

We are a staffing company finding positions for dedicated nurses and physicians.

Target Market(s)

Business Professionals

Industry/Entity Type

Staffing

Contact Information for Business Card

Gordon Pratley
Chairman
417 39th Avenue South
SAINT PETERSBURG FL 33712
813-555-4172 Mobile
813-555-8036 Fax
gpratley@brindlestaffing.com
www.brindlestaffing.com

Font styles to use
Sans Serif

Colors
fbee3e
f04a50
f37122

Requirements
Must have
• Logo Attached, see colors below. We'd like to see Yellow, Orange and Red.

```html
<!DOCTYPE html>
<html lang="en">
<head>
<meta charset="utf-8">
<title>BrindleStaffing Business Card</title>
<link rel="stylesheet" href="https://fonts.googleapis.com/css2?family=Source+Sans+3:wght@400;600;700&display=swap">
<style>
  :root {
    --stage: #1c1c1c;
    --card-black: #020202;
    --brand-yellow: #fbee3e;
    --brand-orange: #f37122;
    --brand-red: #f04a50;
    --text-white: #ffffff;
    --text-dark: #1a1a1a;
  }
  * { box-sizing: border-box; margin: 0; padding: 0; }
  html, body {
    width: 1200px; height: 960px; overflow: hidden;
    background: var(--stage);
    font-family: "Source Sans 3", sans-serif;
  }
  .stage {
    position: relative; width: 1200px; height: 960px;
    display: flex; flex-direction: column; align-items: center; justify-content: center; gap: 60px;
  }
  .card {
    position: relative; width: 560px; height: 320px;
    background: var(--card-black); overflow: hidden;
    box-shadow: 0 18px 40px rgba(0,0,0,.55);
  }
  .brand-name {
    font-weight: 700; color: var(--brand-yellow); letter-spacing: -0.5px; line-height: 1; white-space: nowrap;
  }
  /* front */
  .card-front { display: flex; flex-direction: column; align-items: center; justify-content: center; gap: 22px; }
  .card-front .brand-name { font-size: 58px; }
  .card-front .website { color: var(--text-white); font-size: 17px; letter-spacing: 2.5px; }
  /* back */
  .wave { position: absolute; inset: 0; width: 100%; height: 100%; }
  .card-back .brand-name { position: absolute; left: 30px; top: 92px; font-size: 36px; }
  .contact {
    position: absolute; right: 28px; top: 30px; text-align: right;
    color: var(--text-dark); font-size: 14px; line-height: 1.35; white-space: nowrap;
  }
  .contact .person-name { font-weight: 700; font-size: 19px; }
  .contact .person-title { font-size: 16px; margin-bottom: 10px; }
  .contact .address { margin-bottom: 10px; }
  .contact-line { display: flex; align-items: center; justify-content: flex-end; gap: 7px; }
  .contact-line svg { width: 13px; height: 13px; flex: none; }
</style>
</head>
<body>
<main class="stage">
  <section class="card card-front">
    <div class="brand-name">BrindleStaffing</div>
    <div class="website">www.brindlestaffing.com</div>
  </section>

  <section class="card card-back">
    <svg class="wave" viewBox="0 0 560 320" preserveAspectRatio="none" aria-hidden="true">
      <path d="M320 0 C 352 110, 322 190, 222 240 C 152 275, 100 300, 52 320 L 560 320 L 560 0 Z" fill="var(--brand-red)"/>
      <path d="M342 0 C 374 115, 346 205, 250 252 C 184 284, 132 306, 88 320 L 560 320 L 560 0 Z" fill="var(--brand-orange)"/>
      <path d="M364 0 C 396 120, 372 218, 280 264 C 220 292, 170 310, 124 320 L 560 320 L 560 0 Z" fill="var(--brand-yellow)"/>
    </svg>
    <div class="brand-name">BrindleStaffing</div>
    <div class="contact">
      <div class="person-name">Gordon Pratley</div>
      <div class="person-title">Chairman</div>
      <div class="address">417 39th Avenue South<br>Saint petersburg fl 33712</div>
      <div class="contact-line">813-555-4172
        <svg viewBox="0 0 16 16"><circle cx="8" cy="8" r="7" fill="none" stroke="var(--text-dark)" stroke-width="1.4"/><path d="M5.5 4.5 l1.5 0 0.6 2 -1 0.8 a5 5 0 0 0 2.1 2.1 l0.8 -1 2 0.6 0 1.5 a1 1 0 0 1 -1 1 A6 6 0 0 1 4.5 5.5 a1 1 0 0 1 1 -1z" fill="var(--text-dark)"/></svg>
      </div>
      <div class="contact-line">gpratley@brindlestaffing.com
        <svg viewBox="0 0 16 16"><rect x="1.5" y="4" width="13" height="9" fill="var(--text-dark)"/><path d="M1.5 4 L8 9 L14.5 4" fill="none" stroke="var(--brand-yellow)" stroke-width="1.3"/></svg>
      </div>
      <div class="contact-line">www.brindlestaffing.com
        <svg viewBox="0 0 16 16" fill="none" stroke="var(--text-dark)" stroke-width="1.2"><circle cx="8" cy="8" r="6.5"/><ellipse cx="8" cy="8" rx="3" ry="6.5"/><path d="M1.5 8 H14.5"/></svg>
      </div>
    </div>
  </section>
</main>
</body>
</html>
```